IT Services Company Needs Corporate PPT Template

This is urgent (need a fast turn around). We need a corporate PPT template deck (NOTE: Deck should be in 4:3 ratio) for our IT Services firm that is clean but slick and modern. We tend to lean more towards the flat design look. I'm attaching a zip file which includes our Corporate Branding Guide (which is in progress), color scheme, A PPT deck as inspiration (our logo is on the last slide), our font (LATO). Our newly launched website is located at: http://www.veranthix.com.

As an example of a deck we like see: http://slidemorrow.net/item/clean-multipurpose-business-presentation-template/5318206?WT.ac=category_thumb&WT.seg_1=category_thumb&WT.z_author=PixelHarbor
Although we don't want "this" deck - it gives an idea of style.

I'm also attaching a copy of our corporate deck as it is now to give you an idea of the type of content that would appear on various slides. We definitely want the following slides (at least) within the template:

Title Slide
Blank Slide
2 Column - with bullets
2 Column - no bullets
Single Column - no bullets
Single Column - with bullets
Various Charts and Tables (see example deck)
Meet the Team
Offering Slide
Customer Showcase
Timeline
Case Study
Contact US

Note: Being awarded this job will lead to a second job of creating our corporate deck.

Target Market(s)

CIO, CEO, Technology Officers, Sales People, Marketing, IT heads and staff, Customers, Prospective customers

Industry/Entity Type

Business

Requirements
Must have
• See description and attached files

```html
<!DOCTYPE html>
<html lang="en">
<head>
<meta charset="utf-8">
<title>Project Title here</title>
<link href="https://fonts.googleapis.com/css2?family=Lato:wght@400;700;900&display=swap" rel="stylesheet">
<style>
  :root {
    --header-blue: #115b80;
    --header-blue-light: #1a6a90;
    --slide-title: #5bbcd6;
    --heading-navy: #2b5886;
    --body-grey: #555a5e;
    --footer-top: #f4f4f4;
    --footer-bottom: #e4e4e4;
    --footer-rule: #d6d6d6;
    --presenter-blue: #3a8fd0;
    --brand-navy: #1d3f73;
    --white: #ffffff;
  }
  * { box-sizing: border-box; margin: 0; padding: 0; }
  html, body {
    width: 1200px;
    height: 900px;
    overflow: hidden;
    background: var(--white);
    font-family: "Lato", Arial, sans-serif;
  }
  .slide {
    position: relative;
    width: 1200px;
    height: 900px;
    overflow: hidden;
    background: var(--white);
  }
  .backdrop-texture {
    position: absolute;
    right: 0;
    top: 98px;
    width: 760px;
    height: 720px;
    background: radial-gradient(ellipse at 85% 45%, rgba(200, 210, 222, 0.35) 0%, rgba(225, 231, 238, 0.18) 45%, rgba(255, 255, 255, 0) 75%);
  }
  .header-band {
    position: absolute;
    left: 0; top: 0;
    width: 1200px;
    height: 98px;
    background: linear-gradient(90deg, var(--header-blue) 0%, var(--header-blue-light) 55%, var(--header-blue) 100%);
    display: flex;
    align-items: center;
    padding-left: 33px;
  }
  .project-title {
    color: var(--white);
    font-weight: 700;
    font-size: 39px;
    letter-spacing: 0.2px;
  }
  .content {
    position: absolute;
    left: 36px;
    top: 148px;
    width: 1100px;
  }
  .slide-title {
    color: var(--slide-title);
    font-weight: 700;
    font-size: 33px;
    line-height: 46px;
    margin-bottom: 22px;
  }
  .section { margin-bottom: 52px; }
  .section-heading {
    color: var(--heading-navy);
    font-weight: 700;
    font-size: 26px;
    line-height: 34px;
    margin-bottom: 10px;
  }
  .section-body {
    color: var(--body-grey);
    font-size: 20.5px;
    line-height: 30px;
  }
  .section-body span { display: block; white-space: nowrap; }
  .footer-band {
    position: absolute;
    left: 0; bottom: 0;
    width: 1200px;
    height: 82px;
    background: linear-gradient(180deg, var(--footer-top) 0%, var(--footer-bottom) 100%);
    border-top: 2px solid var(--footer-rule);
    display: flex;
    align-items: center;
    justify-content: space-between;
    padding: 0 18px 0 24px;
  }
  .brand-name {
    color: var(--brand-navy);
    font-weight: 900;
    font-size: 34px;
    letter-spacing: 0.5px;
  }
  .presenter {
    display: flex;
    align-items: baseline;
    gap: 8px;
    color: var(--presenter-blue);
    padding-top: 6px;
  }
  .presenter-label { font-size: 18px; }
  .presenter-name { font-weight: 700; font-size: 22px; }
</style>
</head>
<body>
<div class="slide">
  <div class="backdrop-texture" role="img" aria-label="Faint halftone dot texture fading across the right side of the slide"></div>

  <header class="header-band">
    <h1 class="project-title">Project Title here</h1>
  </header>

  <main class="content">
    <h2 class="slide-title">2 Col slide title here</h2>

    <section class="section">
      <h3 class="section-heading">Bullet Slide Heading Title Here</h3>
      <p class="section-body">
        <span>Lorem ipsum dolor sit Lorem ipsum dolor sit&nbsp; Lorem ipsum dolor sit Lorem ipsum dolor sit&nbsp; Lorem ipsum dolor sit</span>
        <span>Lorem ipsum dolor sit Lorem ipsum dolor sit.&nbsp; Lorem ipsum dolor sit&nbsp; Lorem ipsum dolor sit Lorem ipsum dolor sit</span>
        <span>Lorem ipsum&nbsp; Lorem ipsum dolor sit Lorem ipsum dolor sit</span>
      </p>
    </section>

    <section class="section">
      <h3 class="section-heading">Bullet Slide Heading Title Here</h3>
      <p class="section-body">
        <span>Lorem ipsum dolor sit Lorem ipsum dolor sit&nbsp; Lorem ipsum dolor sit Lorem ipsum dolor sit&nbsp; Lorem ipsum dolor sit</span>
        <span>Lorem ipsum dolor sit Lorem ipsum dolor sit.&nbsp; Lorem ipsum dolor sit&nbsp; Lorem ipsum dolor sit Lorem ipsum dolor sit</span>
        <span>Lorem ipsum&nbsp; Lorem ipsum dolor sit Lorem ipsum dolor sit</span>
      </p>
    </section>

    <section class="section">
      <h3 class="section-heading">Bullet Slide Heading Title Here</h3>
      <p class="section-body">
        <span>Lorem ipsum dolor sit Lorem ipsum dolor sit&nbsp; Lorem ipsum dolor sit Lorem ipsum dolor sit&nbsp; Lorem ipsum dolor sit</span>
        <span>Lorem ipsum dolor sit Lorem ipsum dolor sit.&nbsp; Lorem ipsum dolor sit&nbsp; Lorem ipsum dolor sit Lorem ipsum dolor sit</span>
        <span>Lorem ipsum&nbsp; Lorem ipsum dolor sit Lorem ipsum dolor sit</span>
      </p>
    </section>
  </main>

  <footer class="footer-band">
    <div class="brand-name">Veranthix</div>
    <div class="presenter">
      <span class="presenter-label">Persentator Name&nbsp; :</span>
      <span class="presenter-name">Lena Corvath</span>
    </div>
  </footer>
</div>
</body>
</html>
```